Silver Bloom Marisol's Cleaning Service Business Cards Project

A business card with all contact details with logo design on there (already have a logo) eye catching Logo and contact info on one side, full logo on the back, must target upper class residential and corporate companies, fitness companies, still keep it on the feminine side of things , must look elegant

Target Market(s)

Upper class homes and corporate companies

Industry/Entity Type

Cleaning Service

Contact Information for Business Card

Name: Marisol Quenby
Position: Director
ABN: 31647209853
Email: marisolssilvercleaning@tidymail.example
Number: 0417906354

Font styles to use
Decorative

Colors

Designer to choose colors to be used in the design.

Requirements
Must have
• Available Sydney Wide, contact info and logo on one side, full logo on the back
Nice to have
• Professional appearance
Should not have
• Cheap advert looking stuff

```html
<!DOCTYPE html>
<html lang="en">
<head>
<meta charset="utf-8">
<title>Silver Bloom Marisol's Cleaning Service – Business Cards</title>
<link rel="stylesheet" href="https://fonts.googleapis.com/css2?family=Cinzel:wght@500&family=Roboto:wght@400;500&display=swap">
<style>
  :root {
    --backdrop: #3b3d42;
    --card: #2d323f;
    --accent: #3de3d3;
    --ink: #f1f3f5;
    --rule: #5a6072;
  }
  * { margin: 0; padding: 0; box-sizing: border-box; }
  html, body {
    width: 1200px;
    height: 960px;
    overflow: hidden;
    background: var(--backdrop);
    font-family: "Roboto", Arial, sans-serif;
  }
  .card {
    position: absolute;
    left: 320px;
    width: 600px;
    height: 342px;
    background: var(--card);
    box-shadow: 0 4px 14px rgba(0, 0, 0, 0.45);
  }
  .card--front { top: 110px; }
  .card--back  { top: 493px; }

  .brand {
    position: absolute;
    display: flex;
    flex-direction: column;
    align-items: center;
    text-align: center;
    color: var(--accent);
    font-family: "Cinzel", "Times New Roman", serif;
    font-weight: 500;
  }
  .brand__dot {
    border-radius: 50%;
    background: var(--accent);
  }
  .brand__title, .brand__tagline { display: block; white-space: nowrap; }

  .card--front .brand {
    left: 32px;
    top: 118px;
    width: 240px;
  }
  .card--front .brand__dot { width: 40px; height: 40px; margin-bottom: 34px; }
  .card--front .brand__title { font-size: 19px; line-height: 22px; letter-spacing: 0.5px; }
  .card--front .brand__tagline { margin-top: 3px; font-size: 8.5px; line-height: 12px; letter-spacing: 1.6px; }

  .divider {
    position: absolute;
    left: 275px;
    top: 88px;
    width: 1px;
    height: 160px;
    background: var(--rule);
  }

  .contact {
    position: absolute;
    left: 306px;
    top: 98px;
    color: var(--ink);
  }
  .contact__name {
    color: var(--accent);
    font-size: 20px;
    font-weight: 500;
    line-height: 24px;
    text-transform: uppercase;
  }
  .contact__role {
    color: var(--accent);
    font-size: 14.5px;
    font-weight: 500;
    line-height: 18px;
    text-transform: uppercase;
  }
  .contact__abn {
    margin-top: 14px;
    font-size: 14px;
    line-height: 18px;
  }
  .contact__list {
    list-style: none;
    margin-top: 10px;
  }
  .contact__item {
    display: flex;
    align-items: center;
    gap: 9px;
    font-size: 13.5px;
    line-height: 19.5px;
  }
  .contact__item svg { width: 13px; height: 13px; fill: var(--accent); flex: none; }

  .card--back .brand {
    left: 0;
    top: 72px;
    width: 600px;
  }
  .card--back .brand__dot { width: 80px; height: 80px; margin-bottom: 34px; }
  .card--back .brand__title { font-size: 30px; line-height: 34px; letter-spacing: 1px; }
  .card--back .brand__tagline { margin-top: 6px; font-size: 12px; line-height: 16px; letter-spacing: 2.6px; }

  .back__web {
    position: absolute;
    left: 0;
    top: 288px;
    width: 600px;
    text-align: center;
    color: var(--ink);
    font-size: 15px;
    letter-spacing: 3.5px;
  }
</style>
</head>
<body>
  <section class="card card--front">
    <div class="brand">
      <span class="brand__dot"></span>
      <span class="brand__title">SILVER BLOOM</span>
      <span class="brand__tagline">MARISOL'S CLEANING SERVICE</span>
    </div>
    <div class="divider"></div>
    <div class="contact">
      <p class="contact__name">Marisol Quenby</p>
      <p class="contact__role">Director</p>
      <p class="contact__abn">ABN: 31647209853</p>
      <ul class="contact__list">
        <li class="contact__item">
          <svg viewBox="0 0 24 24" aria-hidden="true"><path d="M6.6 10.8a15.2 15.2 0 0 0 6.6 6.6l2.2-2.2c.3-.3.7-.4 1-.2 1.1.4 2.3.6 3.6.6.6 0 1 .4 1 1V20c0 .6-.4 1-1 1A17 17 0 0 1 3 4c0-.6.4-1 1-1h3.5c.6 0 1 .4 1 1 0 1.3.2 2.5.6 3.6.1.3 0 .7-.2 1z"/></svg>
          <span>0417906354</span>
        </li>
        <li class="contact__item">
          <svg viewBox="0 0 24 24" aria-hidden="true"><path d="M2 5h20v14H2z"/><path d="M3 6l9 6.3L21 6" fill="none" stroke="#2d323f" stroke-width="1.8"/></svg>
          <span>marisolssilvercleaning@tidymail.example</span>
        </li>
        <li class="contact__item">
          <svg viewBox="0 0 24 24" aria-hidden="true"><circle cx="12" cy="12" r="10"/><path d="M7 8c2 0 3 1 3 3s-2 2-2 4-2 1-3-1M15 5c-1 2 1 3 2 4s3 1 3 3" stroke="#2d323f" stroke-width="1.6" fill="none"/></svg>
          <span>www.silverbloom.example</span>
        </li>
      </ul>
    </div>
  </section>

  <section class="card card--back">
    <div class="brand">
      <span class="brand__dot"></span>
      <span class="brand__title">SILVER BLOOM</span>
      <span class="brand__tagline">MARISOL'S CLEANING SERVICE</span>
    </div>
    <p class="back__web">www.silverbloom.example</p>
  </section>
</body>
</html>
```